Website for new dental office

I am Dr. Colin Ashford and am building a new dental practice. I specialize in general dentistry. I am young and have a higher end dental practice incorporating very new technologies and would like my website to reflect that. As many dental patients are older, the website must be very easy to navigate. I would like patients to be able to request appointments, and will eventually add on patient information forms (the health history, etc, that you normally fill out in the practice) from my practice management software, so leave an area for that.

Industry/Entity Type

Building

```html
<!DOCTYPE html>
<html lang="en">
<head>
<meta charset="utf-8">
<title>Ashford Dental</title>
<link rel="stylesheet" href="https://fonts.googleapis.com/css2?family=Arimo:wght@400;700&display=swap">
<style>
:root{
  --blue:#1b7fb8;
  --blue-dark:#10618f;
  --blue-text:#1a73a8;
  --ink:#222;
  --muted:#666;
  --green:#7fcf10;
  --green-dark:#4d9a06;
  --panel-dark:#6b6e72;
  --panel-light:#c9cacc;
  --footer:#e9e9ea;
  --rule:#d6d6d6;
}
*{box-sizing:border-box;margin:0;padding:0}
html,body{width:780px;height:1200px;overflow:hidden}
body{position:relative;background:#fff;font-family:Arimo,Arial,sans-serif;color:var(--ink)}
.abs{position:absolute}
.header-band{left:0;top:0;width:780px;height:330px}
.brand{left:64px;top:22px;display:flex;align-items:center;gap:8px}
.brand-dot{width:30px;height:30px;border-radius:50%;background:#fff}
.brand-name{font-size:19px;font-weight:700;color:#fff;line-height:1.05;width:70px}
.nav{left:311px;top:41px;display:flex;align-items:center;height:19px}
.nav a{font-size:10px;color:#fff;text-decoration:none;margin-right:32px}
.nav a.active{background:#fff;color:var(--blue);padding:4px 11px;margin-right:14px}
.slider-frame{left:64px;top:82px;width:651px;height:322px;background:#fff;border:1px solid #ddd;border-radius:8px;box-shadow:0 10px 18px -10px rgba(0,0,0,.35)}
.slider-photo{left:70px;top:88px;width:639px;height:309px;border-radius:6px;background:linear-gradient(90deg,#8a8c8e 0%,#c9c6c2 45%,#e8d8c8 75%,#d9cbbd 100%)}
.caption{left:90px;top:181px;width:351px;height:176px;background:rgba(170,170,170,.75)}
.caption h1{position:absolute;left:22px;top:34px;font-size:34px;font-weight:400;color:#fff;letter-spacing:.5px;white-space:nowrap}
.caption p{position:absolute;left:25px;top:70px;width:320px;font-size:8.6px;line-height:14px;color:#fff}
.cta{left:126px;top:295px;width:151px;height:47px;background:linear-gradient(#b8f03a,var(--green) 55%,#5fb304);border:1px solid #b9e86a;border-radius:4px;box-shadow:0 2px 4px rgba(0,0,0,.3)}
.cta span{position:absolute;left:46px;top:6px;font-size:14.5px;font-weight:700;color:#20380a;line-height:16px}
.cta svg{position:absolute;left:8px;top:2px}
.dots{left:340px;top:420px;display:flex;gap:4px}
.dots i{width:6px;height:6px;border-radius:50%;background:var(--blue-dark)}
.dots i:nth-child(2){background:#777}
.intro-mark{left:68px;top:454px;width:18px;height:18px;border-radius:50%;background:var(--blue)}
.intro-title{left:96px;top:457px;font-size:14.5px;color:var(--blue-dark)}
.intro-text{left:70px;top:486px;width:642px;font-size:7.6px;line-height:11.7px;color:var(--muted)}
.read-more{left:70px;top:548px;font-size:7.6px;color:var(--blue-text)}
.divider{left:65px;top:578px;width:456px;height:3px;background:#ddd}
.sec-title{font-size:15px;color:var(--blue-text)}
.sec-title b{font-weight:400;color:var(--ink)}
.photo-fill{background:linear-gradient(120deg,#2f9a93,#cfd8d6 60%,#c4a08a)}
.post-title{font-size:9.6px;color:#333}
.post-meta{font-size:6.5px;color:#888}
.post-body{font-size:7.6px;line-height:11.6px;color:var(--muted)}
.rule{height:1px;background:var(--rule)}
.sidebar-dark{left:521px;top:578px;width:191px;height:265px;background:var(--panel-dark)}
.sidebar-light{left:521px;top:843px;width:191px;height:189px;background:var(--panel-light)}
.ribbon{left:529px;top:591px;width:184px;height:34px;background:linear-gradient(#2aa0dc,#1583c2);clip-path:polygon(7px 0,100% 0,100% 100%,7px 100%,0 50%)}
.ribbon span{position:absolute;left:10px;top:9px;font-size:14.5px;color:#fff}
.side-note{left:539px;top:637px;width:165px;font-size:7.2px;line-height:9px;color:#fff}
.field{background:#fff;border:1px solid #bbb;font-size:7.3px;color:#999;padding:6px 6px}
.field em{color:#d00;font-style:normal}
.send{left:541px;top:780px;width:151px;height:25px;background:linear-gradient(#8fdc2a,var(--green-dark));text-align:center;font-size:14px;font-weight:700;color:#fff;line-height:25px}
.call-tag{left:517px;top:843px;width:66px;height:22px;background:#1d8fd0;font-size:9px;font-weight:700;color:#fff;line-height:22px;padding-left:6px;clip-path:polygon(0 0,88% 0,100% 50%,88% 100%,0 100%)}
.phone{left:588px;top:846px;font-size:15px;color:#555}
.hours{left:586px;top:882px;font-size:7.4px;line-height:13px;color:#333}
.hours .open{color:var(--blue-text);font-weight:700;font-size:9px}
.hours b{font-weight:700}
.eforms{left:555px;top:993px;width:115px;height:24px;background:linear-gradient(#fff,#e6e6e6);border:1px solid #aaa;border-radius:12px;font-size:14px;font-weight:700;color:var(--blue-text);line-height:22px;padding-left:31px}
.eforms i{position:absolute;left:13px;top:3px;width:14px;height:16px;background:#f4f0dc;border:1px solid #999}
.list{font-size:7.8px;line-height:11px;color:#333;list-style:none}
.list li{padding-left:9px;position:relative}
.list li::before{content:"";position:absolute;left:0;top:3px;width:4px;height:4px;background:#1d8fd0}
.small-link{font-size:6.6px;color:#2a9a3a;letter-spacing:.3px}
.footer{left:0;top:1032px;width:780px;height:168px;background:var(--footer)}
.f-title{font-size:10.5px;color:var(--blue-text)}
.f-col{font-size:6.6px;line-height:11.7px;color:#555}
.f-col .link{color:#1d8fd0}
.vsep{width:1px;height:116px;background:#cfcfcf}
.f-input{width:100px;height:15px;background:#fff;border:1px solid #ccc;font-size:6.6px;color:#999;padding:3px 5px}
.f-btn{width:40px;height:15px;background:#1d8fd0;font-size:6.6px;font-weight:700;color:#fff;text-align:center;line-height:15px}
</style>
</head>
<body>

<svg class="abs header-band" width="780" height="330" viewBox="0 0 780 330" aria-hidden="true">
  <defs><linearGradient id="hb" x1="0" y1="0" x2="0" y2="1"><stop offset="0" stop-color="#1a7cb6"/><stop offset="1" stop-color="#2d8fc6"/></linearGradient></defs>
  <path d="M0 0H780V305Q700 290 640 300L140 300Q70 295 0 315Z" fill="url(#hb)"/>
</svg>

<div class="abs brand"><span class="brand-dot"></span><span class="brand-name">Ashford Dental</span></div>

<nav class="abs nav">
  <a class="active" href="#">Home</a><a href="#">Dentists Staff</a><a href="#">Services</a><a href="#">Location</a><a href="#">Specialist</a><a href="#" style="margin-right:0">Contact</a>
</nav>

<div class="abs slider-frame"></div>
<div class="abs slider-photo" role="img" aria-label="Smiling senior dental patient with a dentist treating a patient in the background"></div>
<div class="abs caption">
  <h1>Healthy Mouth Life</h1>
  <p>simply dummy text of the printing and typesetting industry. Lorem Ipsum has been the industry's standard dummy text ever since the 1500s,</p>
</div>
<div class="abs cta">
  <svg width="30" height="40" viewBox="0 0 30 40" aria-hidden="true"><path d="M8 0H22V20H30L15 38L0 20H8Z" fill="#d8ff8a" opacity=".8"/></svg>
  <span>Request<br>Appointment</span>
</div>
<div class="abs dots"><i></i><i></i><i></i></div>

<span class="abs intro-mark"></span>
<div class="abs intro-title">Ashford Dental</div>
<p class="abs intro-text">Vestibulum rutrum pharetra diam, eget dapibus leo vehicula ut. Fusce aliquam, odio eget adipiscing lobortis.Vestibulum rutrum pharetra diam, eget dapibus leo vehicula ut. Fusce aliquam, odio eget adipiscing lobortis.Vestibulum rutrum pharetra diam, eget dapibus leo vehicula ut. Fusce aliquam, odio eget adipiscing lobortis.Vestibulum rutrum pharetra diam, eget dapibus leo vehicula ut. Fusce aliquam, odio eget adipiscing lobortis.Vestibulum rutrum pharetra diam, eget dapibus leo vehicula ut. Fusce aliquam, odio eget adipiscing lobortis.Vestibulum rutrum pharetra diam, eget dapibus leo vehicula ut. Fusce aliquam, odio eget adipiscing lobortis.</p>
<div class="abs read-more">[ read More + ]</div>

<div class="abs divider"></div>

<!-- Health Blog -->
<div class="abs sec-title" style="left:65px;top:595px">Health <b>Blog</b></div>
<div class="abs photo-fill" style="left:65px;top:617px;width:203px;height:91px" role="img" aria-label="Dentist in scrubs examining a smiling patient"></div>
<div class="abs post-title" style="left:66px;top:717px">Pellentesque convallis tellus at turpis</div>
<p class="abs post-body" style="left:66px;top:735px;width:195px">Pellentesque convallis tellus at turpis dignissim sit amet cursus erat consectetur. Morbi non neque</p>
<div class="abs rule" style="left:66px;top:765px;width:202px"></div>
<div class="abs post-title" style="left:66px;top:774px">Nullam dapibus neque aliquam quam</div>
<p class="abs post-body" style="left:66px;top:792px;width:195px">Nullam dapibus neque aliquam quam porta sit amet tempor felis mattis. Nullam non elit lectus, sit amet</p>

<!-- Health News -->
<div class="abs sec-title" style="left:276px;top:595px">Health <b style="color:var(--blue-text)">News</b></div>
<div class="abs" style="left:277px;top:617px;width:201px;height:91px;background:linear-gradient(120deg,#3b5d8c,#dcdfe4 45%,#e8c4b0 80%,#c9a7a0)" role="img" aria-label="Dentist treating a patient with open mouth"></div>
<div class="abs post-title" style="left:278px;top:717px">Pellentesque convallis tellus at turpis</div>
<div class="abs post-meta" style="left:278px;top:738px">March 29, 2013 &nbsp;|&nbsp; 4 Comments</div>
<p class="abs post-body" style="left:278px;top:747px;width:195px">Pellentesque convallis tellus at turpis dignissim</p>
<div class="abs rule" style="left:278px;top:765px;width:200px"></div>
<div class="abs post-title" style="left:278px;top:774px">Nullam dapibus neque aliquam quam</div>
<div class="abs post-meta" style="left:278px;top:795px">March 29, 2013 &nbsp;|&nbsp; No Comments</div>
<p class="abs post-body" style="left:278px;top:804px;width:195px">Nullam dapibus neque aliquam quam porta sit amet tempor</p>

<!-- Sidebar form -->
<div class="abs sidebar-dark"></div>
<div class="abs sidebar-light"></div>
<div class="abs ribbon"><span>Send Your Health History</span></div>
<p class="abs side-note">You can find the full contact form under the "Contact us" menu!</p>
<div class="abs field" style="left:541px;top:667px;width:57px;height:19px;padding:5px 5px">Title</div>
<div class="abs" style="left:580px;top:667px;width:18px;height:19px;background:#777"><svg width="18" height="19" aria-hidden="true"><path d="M5 8l4 4 4-4" stroke="#fff" stroke-width="1.6" fill="none"/></svg></div>
<div class="abs field" style="left:541px;top:691px;width:151px;height:19px;padding:4px 6px">First name<em>*</em></div>
<div class="abs field" style="left:541px;top:714px;width:151px;height:19px;padding:4px 6px">Surname<em>*</em></div>
<div class="abs field" style="left:541px;top:737px;width:151px;height:42px;padding:4px 6px">Your health details<em>*</em></div>
<div class="abs send">Send Now!</div>

<div class="abs call-tag">CALL NOW!</div>
<div class="abs phone">(555)-014-2870</div>
<div class="abs hours">
  <span class="open">Open :</span><br>
  <b>Monday - Friday:</b><br>By Appointment Only<br>
  <b>Saturday:</b><br>By Appointment Only<br>
  <b>Sunday (seasonal):</b><br>Closed
</div>
<div class="abs eforms"><i></i>E-Forms</div>

<!-- Services & Products -->
<div class="abs sec-title" style="left:65px;top:852px;line-height:20px">Our Feature<br><b>Services</b></div>
<div class="abs rule" style="left:65px;top:898px;width:187px"></div>
<p class="abs" style="left:65px;top:910px;width:180px;font-size:7.8px;line-height:11px;color:#222">At vero eos et accusamus et iusto odio dignissimos ducimus.</p>
<ul class="abs list" style="left:66px;top:940px;width:88px">
  <li>Soothing Sedation</li><li>Beautiful Porcelain Veneers</li><li>Easy Invisable Braces</li>
</ul>
<ul class="abs list" style="left:155px;top:940px;width:100px">
  <li>Mini Dental Implants</li><li>Brilliant Teeth Whitening</li><li>Safe Digital X-Rays</li>
</ul>
<div class="abs small-link" style="left:65px;top:1009px">READ MORE &#9656;</div>

<div class="abs sec-title" style="left:276px;top:852px;line-height:20px">Innovative<br><b>Products</b></div>
<div class="abs rule" style="left:276px;top:898px;width:184px"></div>
<div class="abs" style="left:273px;top:909px;width:187px;height:92px;background:linear-gradient(110deg,#e7d2c6,#d9a99a 50%,#c5897c 80%,#e9d6cc)" role="img" aria-label="Close-up of a clear teeth aligner being fitted"></div>
<div class="abs small-link" style="left:273px;top:1009px">MORE VIDEOS &#9656;</div>

<!-- Footer -->
<div class="abs footer"></div>
<div class="abs f-title" style="left:77px;top:1067px">Site Map</div>
<div class="abs f-col" style="left:78px;top:1088px">Home<br>Meet the Doctor<br>Our Office<br>Services<br>Smile Gallery<br>Patient Resources<br>Contact Us</div>
<div class="abs vsep" style="left:156px;top:1066px"></div>

<div class="abs f-title" style="left:174px;top:1067px">Follow with us</div>
<div class="abs f-col" style="left:176px;top:1088px">12/07/2013<br>is simply dummy text of the<br><span class="link">setting industry. Lorem Ipsum</span><br><br>12/07/2013<br>is simply dummy text of the<br><span class="link">setting industry. Lorem Ipsum</span></div>
<div class="abs vsep" style="left:297px;top:1066px"></div>

<div class="abs f-title" style="left:315px;top:1065px">Subscribe</div>
<div class="abs f-input" style="left:316px;top:1092px">Enter Your Name</div>
<div class="abs f-input" style="left:316px;top:1110px">Enter Your Email ID</div>
<div class="abs f-btn" style="left:316px;top:1130px">SUBMIT</div>
<div class="abs vsep" style="left:433px;top:1066px"></div>

<div class="abs f-title" style="left:449px;top:1064px">Location</div>
<div class="abs" style="left:451px;top:1092px;width:115px;height:53px;background:linear-gradient(135deg,#e2e2e2,#d2d2d2);border:1px solid #bbb" role="img" aria-label="Street map showing the office location"></div>
<div class="abs f-col" style="left:451px;top:1153px;width:120px">2140 Linden Park Rd #100<br>Brookfield, TN 38200</div>
<div class="abs vsep" style="left:586px;top:1066px"></div>

<div class="abs f-title" style="left:612px;top:1066px">Copyright</div>
<div class="abs" style="left:612px;top:1092px;display:flex;align-items:center;gap:6px">
  <span style="width:22px;height:22px;border-radius:50%;background:var(--blue)"></span>
  <span style="font-size:13px;font-weight:700;color:var(--blue-text);line-height:14px;width:60px">Ashford Dental</span>
</div>
<div class="abs f-col" style="left:612px;top:1137px">©2013 All rights reserved</div>

</body>
</html>
```